Elegant Business Card for Technology Company

Client is a supplier of innovative industrial communications and automation equipment since 2002. This contest is to gather fresh ideas for a redesign of the existing business card. Client is looking for design that best communicates tagline "Industrial Networking and Computing Specialist".

Design submissions should look modern, clean, elegant and professional. It should not be cluttered. Use white as the primary colour. Orange and black as secondary colour. Refer to jpeg File 1 on the current design.

Fonts used by Client used include Arial Regular, Arial Black, Roboto Regular, Roboto Black and Lato.

The winning design will be sent for offset printing using super white 250gsm artcard paper (open for suggestions).

Target Market(s)

System Engineers, Project Managers, Purchasing Managers from companies providing engineering services for Smart Cities.

Industry/Entity Type

Information Technology

Contact Information for Business Card

Refer to PDF File 3 for Business Card Details. Priority of short contact information would be as follows Name > Job Title > Email > Mobile > Web > Tel > Fax > Business Address >UEN (UEN represents company registration number)

Font styles to use
Sans Serif

Colors
ffffff
f37122
000000
5c5c5c

Requirements
Must have
• Refer to AI File 2 (Company Logo) & PDF File 3 (Information on Namecard)
Should not have
• No QR codes
• No Social Media Icons
• Do not create full Black or Orange colour background

```html
<!DOCTYPE html>
<html lang="en">
<head>
<meta charset="utf-8">
<title>Veltra Business Card</title>
<link rel="stylesheet" href="https://fonts.googleapis.com/css2?family=Roboto:wght@400;500;700;900&display=swap">
<style>
  :root {
    --white: #ffffff;
    --orange: #f37122;
    --black: #000000;
    --grey: #5c5c5c;
    --stage: #e9e9e9;
    --dot-tint: #fdeee4;
  }
  * { box-sizing: border-box; margin: 0; padding: 0; }
  html, body { width: 1200px; height: 900px; overflow: hidden; }
  body {
    background: var(--stage);
    font-family: "Roboto", Arial, sans-serif;
    display: flex;
    flex-direction: column;
    align-items: center;
    justify-content: center;
    gap: 36px;
  }
  .card {
    position: relative;
    width: 700px;
    height: 400px;
    background: var(--white);
    border-radius: 22px;
    overflow: hidden;
    box-shadow: 0 6px 18px rgba(0,0,0,.12);
  }
  .card-band { position: absolute; inset: 0; width: 100%; height: 100%; }
  .band-text {
    font-family: "Roboto", Arial, sans-serif;
    fill: var(--white);
    font-size: 17px;
    letter-spacing: .5px;
  }
  .brand {
    position: absolute;
    display: flex;
    align-items: center;
    gap: 14px;
  }
  .brand-dot {
    width: 74px; height: 74px;
    border-radius: 50%;
    background: var(--orange);
  }
  .brand-name {
    font-weight: 900;
    font-size: 58px;
    color: var(--black);
    letter-spacing: 1px;
    line-height: 1;
  }
  /* front */
  .front .brand { left: 70px; top: 150px; }
  .dot-field {
    position: absolute;
    right: 0; top: 0;
    width: 330px; height: 250px;
    background: radial-gradient(ellipse at 70% 30%, var(--dot-tint), rgba(253,238,228,0) 70%);
  }
  .services {
    position: absolute;
    left: 385px; top: 70px;
    list-style: none;
    font-size: 15.5px;
    line-height: 1.25;
    color: var(--black);
  }
  /* back */
  .back .brand { left: 60px; top: 95px; }
  .company {
    position: absolute;
    left: 60px; top: 190px;
    font-size: 17px;
    color: var(--black);
    line-height: 1.3;
  }
  .company .accent { color: var(--orange); font-weight: 700; }
  .company .uen-label { color: var(--orange); }
  .divider {
    position: absolute;
    left: 395px; top: 60px;
    width: 1px; height: 175px;
    background: var(--grey);
    opacity: .6;
  }
  .contact {
    position: absolute;
    left: 420px; top: 58px;
  }
  .person-name { font-weight: 900; font-size: 24px; color: var(--black); }
  .person-title { font-size: 17px; color: var(--orange); margin-bottom: 8px; }
  .contact-list { list-style: none; font-size: 15px; color: var(--black); }
  .contact-list li { display: flex; align-items: center; gap: 10px; line-height: 1.35; }
  .contact-list svg { width: 12px; height: 12px; flex: none; }
</style>
</head>
<body>

<section class="card front">
  <div class="dot-field" role="img" aria-label="Soft orange dot pattern decoration"></div>
  <svg class="card-band" viewBox="0 0 700 400" aria-hidden="true">
    <path d="M0,326 C240,330 480,290 700,205" fill="none" stroke="var(--orange)" stroke-width="5"/>
    <path d="M0,336 C240,340 480,300 700,215 L700,400 L0,400 Z" fill="var(--black)"/>
    <text class="band-text" x="140" y="375">INDUSTRIAL NETWORKING AND COMPUTING SPECIALIST</text>
  </svg>
  <div class="brand">
    <span class="brand-dot"></span>
    <span class="brand-name">VELTRA</span>
  </div>
  <ul class="services">
    <li>Industrial Ethernet / Wireless / Cellular</li>
    <li>Industrial and Embedded Computing</li>
    <li>Serial / Fieldbus Connectivity</li>
    <li>IP Video Surveillance</li>
    <li>Remote Automation</li>
  </ul>
</section>

<section class="card back">
  <svg class="card-band" viewBox="0 0 700 400" aria-hidden="true">
    <path d="M0,326 C240,330 480,290 700,205" fill="none" stroke="var(--orange)" stroke-width="5"/>
    <path d="M0,336 C240,340 480,300 700,215 L700,400 L0,400 Z" fill="var(--black)"/>
    <text class="band-text" x="300" y="345">22 Harbour Lane Tech Centre #04-12</text>
    <text class="band-text" x="330" y="368">(Block B), Singapore 400123</text>
  </svg>
  <div class="brand">
    <span class="brand-dot"></span>
    <span class="brand-name">VELTRA</span>
  </div>
  <p class="company">
    <span class="accent">VELTRA</span> ASIA PACIFIC PTE LTD<br>
    <span class="uen-label">UEN No:</span> 200204417K
  </p>
  <div class="divider"></div>
  <div class="contact">
    <p class="person-name">DANIEL OKAFOR</p>
    <p class="person-title">SALES MANAGER</p>
    <ul class="contact-list">
      <li><svg viewBox="0 0 12 12"><rect x="3" y="0.5" width="6" height="11" rx="1.2" fill="none" stroke="var(--orange)" stroke-width="1.3"/></svg>+65 9123 4567</li>
      <li><svg viewBox="0 0 12 12"><path d="M2,1 L4.5,1 L5.5,3.5 L4,4.8 C4.8,6.6 5.6,7.4 7.2,8 L8.5,6.5 L11,7.5 L11,10 C6,11 1,6 2,1 Z" fill="var(--orange)"/></svg>+65 6555 0140</li>
      <li><svg viewBox="0 0 12 12"><rect x="1" y="4" width="10" height="6" rx="1" fill="var(--orange)"/><rect x="3" y="1" width="6" height="3" fill="none" stroke="var(--orange)" stroke-width="1.2"/></svg>+65 6555 0183</li>
      <li><svg viewBox="0 0 12 12"><rect x="0.7" y="2" width="10.6" height="8" rx="1" fill="none" stroke="var(--orange)" stroke-width="1.3"/><path d="M1,2.5 L6,6.5 L11,2.5" fill="none" stroke="var(--orange)" stroke-width="1.3"/></svg>sales@veltra.example</li>
      <li><svg viewBox="0 0 12 12"><circle cx="6" cy="6" r="5.3" fill="var(--orange)"/><path d="M0.7,6 H11.3 M6,0.7 C3,4 3,8 6,11.3 M6,0.7 C9,4 9,8 6,11.3" fill="none" stroke="var(--white)" stroke-width=".9"/></svg>www.veltra.example</li>
    </ul>
  </div>
</section>

</body>
</html>
```